Clinic for cellulit and fat removal

Name of clinic :
Lirava
- Body & Health (this has to be written on the site.)
I need CMS for me to be able to make changes myself.
A webpage for woman searching for a solution to remove fat and cellulit.
The owner is a brazilian woman in Denmark, and want her sense of aestetic shines thru the website.
There needs to be a slide show on the landing page showing big sliding pictures, of the clinic and and the treatments.
The Cryolipolysis, is a treatment freezing fat and cellulit, and this treatment will be the Attraction of the clinic.
Needs These pages in a horisontal fasion. (written in Danish)
Lirava
Behandlinger
- Cryolipolysis
- Trimflox
- Lymfemassage
- Korathelix
- Amberline Tide
Produkter
Priser
Kontakt
Clinic
Coded - Design and coding required
5+ page

```html
<!DOCTYPE html>
<html lang="da">
<head>
<meta charset="utf-8">
<title>Lirava Body &amp; Health</title>
<link href="https://fonts.googleapis.com/css2?family=Open+Sans:wght@400;600;700&family=Red+Hat+Display:wght@500;700&family=Berkshire+Swash&family=Caveat:wght@500&display=swap" rel="stylesheet">
<style>
:root{
  --magenta:#a8125f;
  --teal:#1bb3bd;
  --lime:#a6cf38;
  --sun:#f9c83d;
  --orange:#f98b45;
  --mint:#8fd0b5;
  --ink:#222;
  --text:#555;
  --muted:#8a8a8a;
  --footer:#333;
  --paper:#fff;
}
*{box-sizing:border-box;margin:0;padding:0}
html,body{width:1200px;height:3093px;overflow:hidden}
body{position:relative;background:var(--paper);font-family:"Open Sans",sans-serif;color:var(--text)}
.abs{position:absolute}

/* header */
.site-header{left:0;top:0;width:1200px;height:117px;background:var(--paper)}
.brand{left:82px;top:26px;display:flex;align-items:center;gap:14px}
.brand-dot{width:26px;height:26px;border-radius:50%;background:var(--teal)}
.brand-name{font-family:"Open Sans",sans-serif;font-weight:600;font-size:30px;line-height:1;color:var(--ink)}
.brand-name small{display:block;font-size:16px;margin-top:6px}
.main-nav{left:412px;top:58px;display:flex;gap:38px;font-size:14px;letter-spacing:.5px;color:#333}
.main-nav a{color:inherit;text-decoration:none}
.main-nav .active{color:var(--magenta)}
.btn-appointment{left:930px;top:50px;width:185px;height:38px;border-radius:19px;background:var(--magenta);color:#fff;font-size:12px;font-weight:700;display:flex;align-items:center;justify-content:center}

/* hero */
.hero{left:0;top:117px;width:1200px;height:563px;background:radial-gradient(circle at 30% 60%,#fff 0%,#ececec 60%,#dcdcdc 100%)}
.hero-photo{left:640px;top:117px;width:380px;height:460px;background:linear-gradient(180deg,#e9c3aa 0%,#d9a98c 60%,#f1f1f1 100%);border-radius:40% 40% 10px 10px}
.hero-title{left:92px;top:262px;font-family:"Berkshire Swash",cursive;font-size:58px;color:#1a1a1a}
.hero-sub{left:92px;top:350px;font-size:18px;color:#666}
.btn{height:38px;border-radius:19px;color:#fff;font-size:13px;font-weight:700;display:flex;align-items:center;justify-content:center}
.btn-know{left:92px;top:400px;width:143px;background:var(--magenta)}
.btn-contact{left:260px;top:400px;width:143px;background:var(--mint)}

/* feature tiles */
.tiles{left:86px;top:577px;width:1029px;height:201px;display:flex}
.tile{flex:1;color:#fff;display:flex;flex-direction:column;align-items:center;padding-top:30px;text-align:center}
.tile svg{width:66px;height:66px;stroke:#fff;fill:none;stroke-width:3}
.tile h3{font-size:15px;font-weight:600;margin-top:22px}
.tile span{font-size:11px;font-weight:700;margin-top:16px}
.t-teal{background:var(--teal)}.t-lime{background:var(--lime)}.t-sun{background:var(--sun)}.t-orange{background:var(--orange)}

/* welcome */
.welcome{left:82px;top:870px;width:570px}
.welcome h2{font-family:"Red Hat Display",sans-serif;font-weight:500;font-size:35px;color:var(--orange)}
.welcome h4{font-size:17px;font-weight:400;color:#3aa89f;margin:4px 0 18px}
.welcome p{font-size:14.5px;line-height:1.68;color:#444;margin-bottom:24px}
.welcome-photo{left:694px;top:888px;width:421px;height:280px;background:linear-gradient(135deg,#d8dde2,#f3f3f3 55%,#c9b8a8)}

/* why choose us */
.why{left:0;top:1273px;width:1200px;height:545px;background:var(--magenta);color:#fff;text-align:center}
.why h2{font-family:"Red Hat Display",sans-serif;font-weight:700;font-size:46px;margin-top:72px}
.why p{font-size:16px;margin-top:4px}
.why-card{top:1492px;width:282px;height:220px}
.why-card .ph{height:173px}
.why-card .lbl{height:47px;background:var(--mint);color:#222;font-family:"Red Hat Display",sans-serif;font-weight:700;font-size:16px;display:flex;align-items:center;justify-content:center;letter-spacing:.3px}

/* stories */
.stories-bg{left:0;top:1818px;width:1200px;height:567px;background:linear-gradient(180deg,#efefef 0%,#e6e6e6 55%,#c9b3a3 78%,#9aa08f 100%)}
.stories-title{left:0;top:1866px;width:1200px;text-align:center;font-family:"Red Hat Display",sans-serif;font-weight:500;font-size:45px;color:#1a1a1a}
.story{top:1976px;width:308px;height:229px;background:#fff;border-bottom:3px solid var(--mint);box-shadow:0 2px 6px rgba(0,0,0,.12);padding:22px 24px}
.story-head{display:flex;align-items:center;gap:16px}
.avatar{width:72px;height:72px;border-radius:50%;background:#d9d2cc;flex:none}
.story-name{font-size:18px;color:#333}
.story-tag{font-family:"Caveat",cursive;font-size:17px;color:#5aa55a}
.story p{font-size:13px;line-height:1.62;color:#999;margin-top:22px}

/* map & contact */
.map{left:0;top:2385px;width:1200px;height:325px;background:linear-gradient(135deg,#eef1f3,#e2e6e9)}
.contact-band{left:0;top:2710px;width:1200px;height:163px;background:var(--mint)}
.contact-card{top:2748px;height:110px;background:#fff;border-radius:4px;display:flex;align-items:center;justify-content:center;flex-direction:column;font-size:17px;color:#444;line-height:1.6;padding-top:14px}
.contact-icon{width:52px;height:52px;border-radius:50%;background:#6f7a77;top:2725px;display:flex;align-items:center;justify-content:center}
.contact-icon svg{width:24px;height:24px;stroke:#fff;fill:none;stroke-width:2}
.socials{display:flex;gap:10px}
.socials i{width:30px;height:30px;border-radius:50%;display:block}

/* footer */
.site-footer{left:0;top:2873px;width:1200px;height:220px;background:var(--footer);color:#ddd;text-align:center}
.footer-brand{display:inline-flex;align-items:center;gap:12px;margin-top:60px;color:#eee}
.footer-brand .brand-name{color:#eee}
.copyright{font-size:11px;margin-top:40px;color:#ccc}
</style>
</head>
<body>

<header class="site-header abs">
  <div class="brand abs"><span class="brand-dot"></span><span class="brand-name">Lirava<small>Body &amp; Health</small></span></div>
  <nav class="main-nav abs">
    <a class="active" href="#">LIRAVA</a><a href="#">BEHANDLINGER</a><a href="#">PRODUKTER</a><a href="#">PRISER</a><a href="#">KONTAKT</a>
  </nav>
  <a class="btn-appointment abs">MAKE AN APPOINTMENT</a>
</header>

<section class="hero abs" role="img" aria-label="Bright clinic backdrop for the cryolipolysis slide"></section>
<div class="hero-photo abs" role="img" aria-label="Slide photo of a woman's waist with dashed contour lines marking treatment areas"></div>
<h1 class="hero-title abs">The Cryolipolysis</h1>
<p class="hero-sub abs">is a treatment freezing fat and cellulit.</p>
<a class="btn btn-know abs">KNOW MORE</a>
<a class="btn btn-contact abs">CONTACT US</a>

<div class="tiles abs">
  <div class="tile t-teal">
    <svg viewBox="0 0 66 66"><circle cx="33" cy="37" r="22"/><path d="M27 8h12M33 8v7M23 36c0-6 10-6 10 0 0-6 10-6 10 0 0 6-10 12-10 12s-10-6-10-12z"/></svg>
    <h3>Health Coach Services</h3><span>READ MORE</span>
  </div>
  <div class="tile t-lime">
    <svg viewBox="0 0 66 66"><circle cx="33" cy="12" r="6"/><path d="M33 20v18M18 30l15 4 15-4M14 50c8-6 30-6 38 0M22 44l11-6 11 6"/></svg>
    <h3>Holistic Approach</h3><span>READ MORE</span>
  </div>
  <div class="tile t-sun">
    <svg viewBox="0 0 66 66"><path d="M22 6c2 14 2 22-2 30s2 22 8 26M44 6c-2 14-2 22 2 30s-2 22-8 26M20 40c8 6 18 6 26 0M6 24h10M50 24h10"/></svg>
    <h3>Fit Body Form</h3><span>READ MORE</span>
  </div>
  <div class="tile t-orange">
    <svg viewBox="0 0 66 66"><rect x="8" y="12" width="50" height="46"/><path d="M8 24h50M20 6v12M46 6v12M18 34h6M30 34h6M42 34h6M18 46h6M30 46h6M42 46h6"/></svg>
    <h3>Health Coach Services</h3><span>READ MORE</span>
  </div>
</div>

<section class="welcome abs">
  <h2>Welcome Lirava Body &amp; Health</h2>
  <h4>The Cryolipolysis, is a treatment freezing fat &amp; cellulit</h4>
  <p>Your Transformation is our passion &amp; We are your personal trainers, trained nutritionist, your supplement experts, your health coach, your support group We Provide technology ut tools great explorers of the truth, the masters of human happiness need burn fat, build become your best self.</p>
  <p>Personalized patient care is what sets Solvang Care Center apart. When you visit one of our four San Francisco campus locations you can expect to receive world class care. Expert physician specialists and caring clinical staff provide you with an exceptional health care experience.</p>
</section>
<div class="welcome-photo abs" role="img" aria-label="Therapist applying the cryolipolysis device to a client's abdomen"></div>

<section class="why abs">
  <h2>Why Choose Us</h2>
  <p>is a treatment freezing fat and cellulit</p>
</section>
<div class="why-card abs" style="left:134px"><div class="ph" role="img" aria-label="Hands smoothing the back of a thigh" style="background:linear-gradient(135deg,#f0ddd0,#cfa58b)"></div><div class="lbl">CRYOLIPOLYSIS TREATMENT</div></div>
<div class="why-card abs" style="left:465px"><div class="ph" role="img" aria-label="Waist with dashed contour arrows" style="background:linear-gradient(135deg,#e8c2a7,#c98f70)"></div><div class="lbl">CRYOLIPOLYSIS TREATMENT</div></div>
<div class="why-card abs" style="left:788px"><div class="ph" role="img" aria-label="Client resting while the cooling applicator works" style="background:linear-gradient(135deg,#cfd6dc,#f2f2f2 60%,#d8c3b3)"></div><div class="lbl">CRYOLIPOLYSIS TREATMENT</div></div>

<section class="stories-bg abs" role="img" aria-label="Treatment room with a client lying under a cryolipolysis applicator"></section>
<h2 class="stories-title abs">Sucessful Stories</h2>
<article class="story abs" style="left:113px">
  <div class="story-head"><div class="avatar"></div><div><div class="story-name">Mirela Santos</div><div class="story-tag">Lost 128 Pounds And 5 Sizes</div></div></div>
  <p>In 10 months of following Health Coach, Joe has lost 128 pounds. If you are overweight, out of shape, and worried that it's too late to ...</p>
</article>
<article class="story abs" style="left:452px">
  <div class="story-head"><div class="avatar"></div><div><div class="story-name">Helena Kovacsova</div><div class="story-tag">Lost 128 Pounds And 5 Sizes</div></div></div>
  <p>Ladies, meet your new hero. Men, prepare to be humbled. My friend Staci, or Spezy as she's known around health Coach, has one of the best ...</p>
</article>
<article class="story abs" style="left:790px">
  <div class="story-head"><div class="avatar"></div><div><div class="story-name">Daniel Ostrow</div><div class="story-tag">Lost 65 Pounds And 5 Sizes</div></div></div>
  <p>Over the past two years, he was able to slowly and steadily bring that down before having an incredible breakthrough that allowed him to transform drastically.</p>
</article>

<section class="map abs" role="img" aria-label="Street map showing the clinic location"></section>
<svg class="abs" style="left:624px;top:2496px" width="30" height="44" viewBox="0 0 30 44"><path d="M15 0C7 0 0 6 0 15c0 11 15 29 15 29s15-18 15-29C30 6 23 0 15 0z" fill="#f0566a"/><circle cx="15" cy="15" r="5" fill="#fff"/></svg>

<section class="contact-band abs"></section>
<div class="contact-card abs" style="left:121px;width:281px">hello@liravabodyhealth.dk</div>
<div class="contact-card abs" style="left:520px;width:216px">0800 4170 236<br>0845 918 2054</div>
<div class="contact-card abs" style="left:790px;width:278px"><div class="socials"><i style="background:#2f4f7a"></i><i style="background:#3fa9d9"></i><i style="background:#f29a1e"></i><i style="background:#a9a9a9"></i></div></div>
<div class="contact-icon abs" style="left:236px"><svg viewBox="0 0 24 24"><rect x="3" y="6" width="18" height="13"/><path d="M3 6l9 7 9-7"/></svg></div>
<div class="contact-icon abs" style="left:602px"><svg viewBox="0 0 24 24"><path d="M5 3h4l2 5-3 2c1 3 3 5 6 6l2-3 5 2v4c0 1-1 2-2 2C10 21 3 14 3 5c0-1 1-2 2-2z"/></svg></div>
<div class="contact-icon abs" style="left:903px"><svg viewBox="0 0 24 24"><circle cx="6" cy="12" r="3"/><circle cx="18" cy="5" r="3"/><circle cx="18" cy="19" r="3"/><path d="M8.5 10.5l7-4M8.5 13.5l7 4"/></svg></div>

<footer class="site-footer abs">
  <div class="footer-brand"><span class="brand-dot" style="background:#888"></span><span class="brand-name">Lirava<small>Body &amp; Health</small></span></div>
  <p class="copyright">Lirava All rights reserved, Copyright 2016-2017</p>
</footer>

</body>
</html>
```